English and Spanish Language School Needs a Business Card

Need a business card design a startup company called Maribel Language School. The company will offer English and Spanish conversational level courses designed to make the learner feel comfortable with grammar and vocabulary. We would like to see a logo with some colour that should communicate learning, growth.

Target Market(s)

Consumers and businesses

Industry/Entity Type

Education

Contact Information for Business Card

TBD

Font styles to use
Serif

Requirements
Must have
• Include the following
• Logo
• Name
• Title
• Cellphone Number
• Office Phone number
• Email address
• Office Address

```html
<!DOCTYPE html>
<html lang="en">
<head>
<meta charset="utf-8">
<title>Maribel Language School – Business Card</title>
<link href="https://fonts.googleapis.com/css2?family=Montserrat:wght@400;500;600;700&display=swap" rel="stylesheet">
<style>
  :root {
    --bg: #2b2b2b;
    --card: #050505;
    --red: #d0202a;
    --teal: #1fb0b8;
    --font: "Montserrat", sans-serif;
  }
  * { margin: 0; padding: 0; box-sizing: border-box; }
  html, body { width: 1200px; height: 900px; overflow: hidden; }
  body { background: var(--bg); font-family: var(--font); position: relative; }

  .card {
    position: absolute;
    width: 560px; height: 320px;
    background: var(--card);
    border-radius: 22px;
    overflow: hidden;
    box-shadow: 0 14px 30px rgba(0,0,0,.45);
  }
  .card-front { left: 70px; top: 80px; }
  .card-back { left: 570px; top: 490px; }

  .card-shapes { position: absolute; inset: 0; }

  .brand-name {
    position: absolute;
    color: var(--red);
    font-weight: 700;
    font-size: 34px;
    line-height: 1;
    white-space: nowrap;
    letter-spacing: -0.5px;
  }
  .card-front .brand-name { left: 0; right: 0; top: 128px; text-align: center; }
  .card-back .brand-name { left: 30px; top: 96px; font-size: 28px; }

  .front-web {
    position: absolute; right: 34px; top: 240px;
    color: var(--red); font-size: 13px; font-weight: 500;
  }

  .holder { position: absolute; right: 30px; top: 34px; text-align: right; }
  .holder-name { color: var(--red); font-size: 21px; font-weight: 600; letter-spacing: .5px; }
  .holder-title { color: var(--teal); font-size: 12px; margin-top: 2px; }
  .address {
    position: absolute; right: 30px; top: 106px; text-align: right;
    color: var(--teal); font-size: 13px; line-height: 1.4;
  }

  .contact-list {
    position: absolute; left: 30px; top: 196px; list-style: none;
    font-size: 13.5px; line-height: 20px;
  }
  .contact-list li { display: flex; align-items: center; gap: 10px; color: var(--teal); }
  .contact-list li.web { color: var(--red); font-weight: 700; }
  .contact-list svg { width: 11px; height: 11px; flex: none; }
</style>
</head>
<body>

<!-- Front of card -->
<section class="card card-front" aria-label="Business card front">
  <svg class="card-shapes" viewBox="0 0 560 320" aria-hidden="true">
    <polygon points="0,262 300,262 340,286 340,320 0,320" fill="var(--red)"/>
    <polygon points="325,262 560,262 560,272 340,272" fill="var(--teal)"/>
  </svg>
  <div class="brand-name">Maribel Language School</div>
  <div class="front-web">www.maribellanguageschool.com</div>
</section>

<!-- Back of card -->
<section class="card card-back" aria-label="Business card back">
  <svg class="card-shapes" viewBox="0 0 560 320" aria-hidden="true">
    <rect x="520" y="0" width="14" height="16" fill="var(--teal)"/>
    <rect x="534" y="0" width="26" height="16" fill="var(--red)"/>
    <line x1="30" y1="188" x2="530" y2="80" stroke="var(--red)" stroke-width="1" opacity="0"/>
    <line x1="330" y1="86" x2="530" y2="86" stroke="var(--red)" stroke-width="1"/>
    <line x1="30" y1="188" x2="300" y2="188" stroke="var(--red)" stroke-width="1"/>
    <polygon points="355,212 560,212 560,270 340,270" fill="var(--red)"/>
    <polygon points="0,298 330,282 340,272 340,290 0,306" fill="var(--teal)"/>
  </svg>

  <div class="brand-name">Maribel Language School</div>

  <div class="holder">
    <div class="holder-name">Lena Hartwell</div>
    <div class="holder-title">Director</div>
  </div>
  <div class="address">Po Box 218<br>Lindale VIC 3905</div>

  <ul class="contact-list">
    <li>
      <svg viewBox="0 0 12 12"><rect x="3" y="0.5" width="6" height="11" rx="1.2" fill="none" stroke="var(--red)" stroke-width="1.2"/></svg>
      +330 5180-2947
    </li>
    <li>
      <svg viewBox="0 0 12 12"><path d="M2.5 1 L4.5 1 L5.2 3.6 L4 4.6 Q5 7 7.4 8 L8.4 6.8 L11 7.5 L11 9.5 Q10.5 11 9 11 Q1 10 1 2.5 Q1 1 2.5 1 Z" fill="var(--red)"/></svg>
      +330 5172-6630
    </li>
    <li>
      <svg viewBox="0 0 12 12"><rect x="0.8" y="2.2" width="10.4" height="7.6" fill="none" stroke="var(--red)" stroke-width="1.1"/><polyline points="0.8,2.4 6,6.6 11.2,2.4" fill="none" stroke="var(--red)" stroke-width="1.1"/></svg>
      hello@maribelschool.com
    </li>
    <li class="web">
      <svg viewBox="0 0 12 12"><circle cx="6" cy="6" r="5.2" fill="none" stroke="var(--red)" stroke-width="1.1"/><ellipse cx="6" cy="6" rx="2.2" ry="5.2" fill="none" stroke="var(--red)" stroke-width="1"/><line x1="0.8" y1="6" x2="11.2" y2="6" stroke="var(--red)" stroke-width="1"/></svg>
      maribellanguageschool.com
    </li>
  </ul>
</section>

</body>
</html>
```